Business Card for a mobile physiotherapy company

I need a layout for a business card for a mobile physiotherapy company.
Slogan is "Mobile Physiotherapy - Your Road To Recovery"
Phone number is 867-555-0142
Email VardenTherapy@postnest.ca (subject to change with website)
Website www.VardenTherapy.ca
My name and credentials: Luke Varden Luke Varden, BSc(kin), MPT, CAFCI, IMS
Information maybe included: Direct Billing, Services including Physiotherapy, IMS, acupuncture
Maybe include facebook and instagram logos
One side with the logo clean and sharp
Other side with details, try not to look too busy, keep everything concise

```html
<!DOCTYPE html>
<html lang="en">
<head>
<meta charset="utf-8">
<title>Varden Therapy – Business Card</title>
<link href="https://fonts.googleapis.com/css2?family=Roboto:wght@400;500;700&display=swap" rel="stylesheet">
<style>
  :root {
    --bg: #dedede;
    --teal: #145c52;
    --teal-mid: #2a6a70;
    --navy: #2b4f7a;
    --ink: #2d3338;
    --white: #ffffff;
    --rule: #3d5d86;
  }
  * { box-sizing: border-box; margin: 0; padding: 0; }
  html, body {
    width: 1200px; height: 900px; overflow: hidden;
    background: var(--bg);
    font-family: "Roboto", Arial, sans-serif;
  }
  .stage {
    width: 1200px; height: 900px;
    display: flex; flex-direction: column;
    align-items: center; justify-content: center; gap: 56px;
  }
  .card {
    width: 640px; height: 366px;
    position: relative; overflow: hidden;
    box-shadow: 0 6px 18px rgba(0,0,0,0.12);
  }

  /* Front */
  .card--front {
    background: linear-gradient(135deg, var(--teal) 0%, var(--teal-mid) 50%, var(--navy) 100%);
    color: var(--white);
    display: flex; flex-direction: column; align-items: center; justify-content: center; gap: 44px;
  }
  .brand {
    display: flex; align-items: center; gap: 14px;
    font-weight: 700; font-size: 46px; letter-spacing: 2px; line-height: 1;
  }
  .brand__mark { width: 18px; height: 18px; background: currentColor; }
  .card--front .brand { color: var(--white); }
  .services {
    display: flex; align-items: center; gap: 18px;
    font-size: 17px; letter-spacing: 0.5px;
  }
  .services__dot { width: 9px; height: 9px; background: var(--white); }

  /* Back */
  .card--back { background: var(--white); }
  .back__body {
    position: absolute; left: 0; right: 0; top: 0; height: 290px;
    display: flex; align-items: center;
  }
  .back__brand {
    width: 318px; display: flex; justify-content: center;
  }
  .card--back .brand { color: var(--teal); font-size: 34px; letter-spacing: 1px; gap: 10px; }
  .card--back .brand__mark { width: 14px; height: 14px; background: var(--navy); }
  .back__rule { width: 1.5px; height: 168px; background: var(--rule); }
  .contact { padding-left: 34px; color: var(--ink); }
  .contact__name { font-weight: 700; font-size: 25px; color: var(--navy); }
  .contact__creds { font-size: 15px; margin-top: 3px; }
  .contact__list { list-style: none; margin-top: 22px; display: flex; flex-direction: column; gap: 7px; }
  .contact__item { display: flex; align-items: center; gap: 10px; font-size: 15px; }
  .contact__icon {
    width: 20px; height: 20px; border-radius: 50%;
    display: flex; align-items: center; justify-content: center; flex-shrink: 0;
  }
  .contact__icon--navy { background: var(--navy); }
  .contact__icon--teal { background: var(--teal); }
  .contact__icon svg { width: 12px; height: 12px; }
  .back__band {
    position: absolute; left: 0; right: 0; bottom: 0; height: 76px;
    background: linear-gradient(90deg, var(--teal) 0%, var(--teal-mid) 55%, var(--navy) 100%);
    color: var(--white);
    display: flex; align-items: center; justify-content: center;
    font-size: 19px; letter-spacing: 0.3px;
  }
</style>
</head>
<body>
<main class="stage">
  <section class="card card--front" aria-label="Card front">
    <div class="brand"><span class="brand__mark"></span>VARDEN THERAPY</div>
    <div class="services">
      <span>Physiotherapy</span><span class="services__dot"></span>
      <span>IMS</span><span class="services__dot"></span>
      <span>Acupuncture</span>
    </div>
  </section>

  <section class="card card--back" aria-label="Card back">
    <div class="back__body">
      <div class="back__brand">
        <div class="brand"><span class="brand__mark"></span>VARDEN THERAPY</div>
      </div>
      <div class="back__rule"></div>
      <div class="contact">
        <div class="contact__name">Luke Varden</div>
        <div class="contact__creds">BSc(kin), MPT, CAFCI, IMS</div>
        <ul class="contact__list">
          <li class="contact__item">
            <span class="contact__icon contact__icon--navy">
              <svg viewBox="0 0 24 24"><path fill="#fff" d="M6.6 10.8a15 15 0 0 0 6.6 6.6l2.2-2.2a1 1 0 0 1 1-.25 11.4 11.4 0 0 0 3.6.57 1 1 0 0 1 1 1V20a1 1 0 0 1-1 1A17 17 0 0 1 3 4a1 1 0 0 1 1-1h3.5a1 1 0 0 1 1 1c0 1.25.2 2.45.57 3.57a1 1 0 0 1-.25 1z"/></svg>
            </span>867-555-0142
          </li>
          <li class="contact__item">
            <span class="contact__icon contact__icon--teal">
              <svg viewBox="0 0 24 24"><rect x="3" y="6" width="18" height="12" fill="none" stroke="#fff" stroke-width="2"/><path d="M3 6l9 7 9-7" fill="none" stroke="#fff" stroke-width="2"/></svg>
            </span>VardenTherapy@postnest.ca
          </li>
          <li class="contact__item">
            <span class="contact__icon contact__icon--navy">
              <svg viewBox="0 0 24 24" fill="none" stroke="#fff" stroke-width="2"><circle cx="12" cy="12" r="9"/><path d="M3 12h18M12 3c3 3 3 15 0 18M12 3c-3 3-3 15 0 18"/></svg>
            </span>www.VardenTherapy.ca
          </li>
        </ul>
      </div>
    </div>
    <div class="back__band">Mobile Physiotherapy - Your Road To Recovery</div>
  </section>
</main>
</body>
</html>
```